Business cards for Zestcycle

We need a business card layout for our new bike and e-bike rental (we also sell used e-bikes and bike accessories). The logo already exists.

```html
<!DOCTYPE html>
<html lang="en">
<head>
<meta charset="utf-8">
<title>Zestcycle Business Cards</title>
<link rel="stylesheet" href="https://fonts.googleapis.com/css2?family=Fira+Sans:wght@300;400;500&family=Roboto:wght@400;700&display=swap">
<style>
  :root {
    --page-bg: #e4e4e4;
    --card-dark: #232e35;
    --card-light: #f7f7f7;
    --teal: #3aa98b;
    --teal-deep: #2e9a7d;
    --ink: #22272b;
    --tagline-light: #e9eef0;
  }
  * { margin: 0; padding: 0; box-sizing: border-box; }
  html, body {
    width: 1200px;
    height: 576px;
    overflow: hidden;
    background: var(--page-bg);
  }
  .canvas {
    position: relative;
    width: 1200px;
    height: 576px;
  }
  .card {
    position: absolute;
    top: 139px;
    width: 484px;
    height: 292px;
    border-radius: 13px;
    overflow: hidden;
  }
  /* Front */
  .card-front {
    left: 82px;
    background: var(--card-dark);
  }
  .front-brand {
    position: absolute;
    left: 0;
    right: 0;
    top: 102px;
    text-align: center;
    font-family: "Fira Sans", sans-serif;
    font-weight: 300;
    font-size: 62px;
    line-height: 1;
    letter-spacing: 1px;
    color: var(--teal);
  }
  .front-tagline {
    position: absolute;
    left: 0;
    right: 0;
    top: 170px;
    text-align: center;
    font-family: "Fira Sans", sans-serif;
    font-weight: 500;
    font-size: 16px;
    color: var(--tagline-light);
  }
  /* Back */
  .card-back {
    left: 603px;
    background: var(--card-light);
  }
  .card-back::after {
    content: "";
    position: absolute;
    left: 0;
    right: 0;
    bottom: 0;
    height: 5px;
    background: linear-gradient(90deg, var(--teal) 0%, var(--teal-deep) 55%, var(--card-dark) 100%);
  }
  .person-name {
    position: absolute;
    left: 272px;
    top: 33px;
    font-family: "Roboto", sans-serif;
    font-weight: 700;
    font-size: 18px;
    color: var(--teal);
  }
  .person-role {
    position: absolute;
    left: 272px;
    top: 57px;
    font-family: "Roboto", sans-serif;
    font-weight: 400;
    font-size: 11px;
    color: var(--ink);
  }
  .back-brand-block {
    position: absolute;
    left: 30px;
    top: 206px;
    text-align: center;
  }
  .back-brand {
    font-family: "Fira Sans", sans-serif;
    font-weight: 300;
    font-size: 38px;
    line-height: 1;
    color: var(--teal);
  }
  .back-tagline {
    margin-top: 5px;
    font-family: "Fira Sans", sans-serif;
    font-weight: 500;
    font-size: 11px;
    color: var(--ink);
  }
  .address {
    position: absolute;
    left: 272px;
    top: 167px;
    font-family: "Fira Sans", sans-serif;
    font-size: 12.5px;
    line-height: 19px;
    color: var(--ink);
  }
  .contact-list {
    position: absolute;
    left: 272px;
    top: 210px;
    list-style: none;
    font-family: "Fira Sans", sans-serif;
    font-size: 12.5px;
    color: var(--ink);
  }
  .contact-item {
    display: flex;
    align-items: center;
    height: 17.5px;
  }
  .contact-icon {
    width: 11px;
    height: 11px;
    margin-right: 12px;
    fill: var(--teal);
  }
</style>
</head>
<body>
<main class="canvas">
  <section class="card card-front" aria-label="Card front">
    <p class="front-brand">ZESTCYCLE</p>
    <p class="front-tagline">e-leicht unterwegs</p>
  </section>

  <section class="card card-back" aria-label="Card back">
    <h1 class="person-name">John Doe Smith</h1>
    <p class="person-role">Managing Director</p>

    <div class="back-brand-block">
      <p class="back-brand">ZESTCYCLE</p>
      <p class="back-tagline">e-leicht unterwegs</p>
    </div>

    <p class="address">234 Anywhere St., Any City,<br>Any Town, US 123456</p>

    <ul class="contact-list">
      <li class="contact-item">
        <svg class="contact-icon" viewBox="0 0 12 12" aria-hidden="true"><path d="M1 4.2C1 2.6 3 1.5 6 1.5s5 1.1 5 2.7v.9H8.3v-1H3.7v1H1z"/><path d="M2.5 6.2h7L10.5 10.5h-9z"/></svg>
        <span>555.555.5555</span>
      </li>
      <li class="contact-item">
        <svg class="contact-icon" viewBox="0 0 12 12" aria-hidden="true"><path d="M0.5 2.5h11v7h-11z" fill="none" stroke="#3aa98b" stroke-width="1.3"/><path d="M0.8 2.8L6 7l5.2-4.2" fill="none" stroke="#3aa98b" stroke-width="1.3"/></svg>
        <span>johndoe@zestcycle-rides.com</span>
      </li>
      <li class="contact-item">
        <svg class="contact-icon" viewBox="0 0 12 12" aria-hidden="true"><circle cx="6" cy="6" r="5.3"/><path d="M0.8 6h10.4M6 0.8v10.4M2 3.4h8M2 8.6h8" stroke="#f7f7f7" stroke-width="0.8" fill="none"/></svg>
        <span>www.zestcycle-rides.com</span>
      </li>
    </ul>
  </section>
</main>
</body>
</html>
```